Dunmore Roofing

Want a professional looking business card

Industry/Entity Type

Business

Contact Information for Business Card

Paul Dunmore ( Owner) paul@dunmoreroofing-example.com, www.dunmoreroofing-example.com, Adress: 4172 Township road 43 Plantagenet,ON K9X4T2

```html
<!DOCTYPE html>
<html lang="en">
<head>
<meta charset="utf-8">
<title>Dunmore Roofing – Business Card</title>
<link href="https://fonts.googleapis.com/css2?family=Roboto+Condensed:wght@300;400;700&display=swap" rel="stylesheet">
<style>
  :root {
    --brand-blue: #1f5fb5;
    --brand-blue-dark: #17479a;
    --brand-blue-light: #2a72c8;
    --paper: #f6f6f4;
    --band-grey: #5b5f66;
    --band-text: #e9ebee;
    --backdrop: #e4e2de;
    --rule: rgba(255,255,255,0.45);
  }
  * { box-sizing: border-box; margin: 0; padding: 0; }
  html, body { width: 1200px; height: 780px; overflow: hidden; }
  body {
    background: var(--backdrop);
    font-family: "Roboto Condensed", "Arial Narrow", sans-serif;
    position: relative;
  }
  .card {
    position: absolute;
    top: 241px;
    width: 520px;
    height: 298px;
    border-radius: 16px;
    overflow: hidden;
    box-shadow: 0 8px 24px rgba(0,0,0,0.18);
  }
  .card--front { left: 50px; display: flex; }
  .card--back {
    left: 630px;
    background: radial-gradient(circle at 55% 45%, var(--brand-blue-light), var(--brand-blue-dark) 80%);
  }

  /* front */
  .front__brand {
    width: 236px;
    flex: none;
    background: var(--paper);
    display: flex;
    align-items: center;
    justify-content: center;
  }
  .front__info {
    flex: 1;
    background: linear-gradient(160deg, var(--brand-blue-light), var(--brand-blue));
    border-left: 4px solid #c9ccd1;
    color: #fff;
    padding: 30px 14px 0;
    display: flex;
    flex-direction: column;
    align-items: center;
    text-align: center;
  }

  .wordmark {
    display: flex;
    align-items: center;
    gap: 10px;
    font-weight: 700;
    text-transform: uppercase;
    letter-spacing: 2px;
    line-height: 1.05;
    white-space: nowrap;
  }
  .wordmark__mark { width: 14px; height: 14px; background: currentColor; flex: none; }
  .wordmark__text span { display: block; }
  .wordmark--front { color: var(--brand-blue); font-size: 34px; }
  .wordmark--back  { color: #fff; font-size: 40px; }

  .owner__name { font-size: 22px; font-weight: 400; }
  .owner__title { font-size: 13px; font-weight: 300; margin-top: 1px; }

  .contact { font-size: 13px; font-weight: 400; line-height: 1.35; white-space: nowrap; }
  .contact__icon { display: block; margin: 10px auto 4px; }
  .contact__rule { width: 150px; height: 1px; background: var(--rule); margin: 8px 0; }
  .contact__web { font-size: 13px; margin-top: 10px; letter-spacing: 0.2px; white-space: nowrap; }
  .contact__web b { font-weight: 700; }

  /* back */
  .back__brand {
    position: absolute;
    left: 0; right: 0; top: 0; bottom: 40px;
    display: flex;
    align-items: center;
    justify-content: center;
  }
  .back__hours {
    position: absolute;
    left: 0; right: 0; bottom: 0;
    height: 40px;
    background: var(--band-grey);
    border-top: 3px solid #d3d6da;
    color: var(--band-text);
    font-size: 14px;
    display: flex;
    align-items: center;
    justify-content: center;
    gap: 6px;
    white-space: nowrap;
  }
  .back__hours b { font-weight: 700; }
</style>
</head>
<body>

  <section class="card card--front" aria-label="Business card front">
    <div class="front__brand">
      <div class="wordmark wordmark--front">
        <span class="wordmark__mark"></span>
        <span class="wordmark__text"><span>Dunmore</span><span>Roofing</span></span>
      </div>
    </div>
    <div class="front__info">
      <p class="owner__name">Paul Dunmore</p>
      <p class="owner__title">Owner</p>

      <svg class="contact__icon" width="16" height="16" viewBox="0 0 16 16" aria-hidden="true">
        <circle cx="8" cy="8" r="8" fill="#fff"/>
        <path d="M5.2 4.2l1.4-.3.9 2-1 .8a5 5 0 0 0 2.3 2.3l.8-1 2 .9-.3 1.4c-3.3.3-6.4-2.8-6.1-6.1z" fill="var(--brand-blue)"/>
      </svg>
      <p class="contact">(555) 555-0147</p>
      <div class="contact__rule"></div>

      <p class="contact">paul@dunmoreroofing-example.com</p>
      <div class="contact__rule"></div>

      <p class="contact">4172 Township road 43<br>Alderbrook, QN K9X4T2</p>
      <p class="contact__web">www.<b>dunmoreroofing-example</b>.com</p>
    </div>
  </section>

  <section class="card card--back" aria-label="Business card back">
    <div class="back__brand">
      <div class="wordmark wordmark--back"><span class="wordmark__mark"></span>Dunmore Roofing</div>
    </div>
    <p class="back__hours">
      <span><b>Monday - Friday</b> : 9am - 5pm</span> |
      <span><b>Saturday</b> : By appointment</span> |
      <span><b>Sunday</b> : Closed</span>
    </p>
  </section>

</body>
</html>
```